Finiding oppertunites in Real Estate 6.15.20

size of ad 7” x 9.6”
1-I like the ad to stand out and attract people's attention.
2-you should be able to see the text of the ad clearly .. see the attachment anything in yellow is instructions.
3-the list of topics should not be the main part of the ad
4-if you decide you want a picture or vector of a person .. (you decide)
then it should be a white male about 25-30 years old wearing a solid white or blue shirt and not long hair.
5-leave 1 inch for footer
see attachment
Good luck

Target Market(s)

potential male students 25-35 years of age

Industry/Entity Type

Education

Requirements
Must have
• will stand out and people would want to see it.
should be able to read the words of ad
Nice to have
• how to make money in real estate on one line

```html
<!DOCTYPE html>
<html lang="en">
<head>
<meta charset="utf-8">
<title>Real Estate Career Course</title>
<link rel="stylesheet" href="https://fonts.googleapis.com/css2?family=Dosis:wght@700;800&family=Nunito:wght@400;600;700&display=swap">
<style>
  :root {
    --navy: #1f2f6b;
    --royal: #2e4fa8;
    --bright: #2b6fd1;
    --teal: #4cc3c4;
    --lilac: #8a7fd6;
    --ice: #e6f3fb;
    --paper: #ffffff;
    --ink: #1d2440;
    --footer-text: #e8eefc;
  }
  * { margin: 0; padding: 0; box-sizing: border-box; }
  html, body { width: 897px; height: 1200px; overflow: hidden; background: var(--paper); }
  .poster {
    position: relative;
    width: 897px; height: 1200px;
    overflow: hidden;
    background: linear-gradient(180deg, var(--paper) 0%, #f4f9fd 45%, var(--ice) 75%, #d3ecf6 100%);
    font-family: "Nunito", sans-serif;
    color: var(--ink);
  }
  .corner-wave { position: absolute; right: 0; top: 0; width: 290px; height: 270px; }
  .headline {
    position: absolute; left: 46px; top: 22px;
    font-family: "Dosis", sans-serif; font-weight: 800;
    font-size: 50px; line-height: 0.98; letter-spacing: 0.5px;
    color: var(--bright); text-transform: uppercase;
  }
  .headline .line-two { display: inline-block; border-bottom: 3px solid var(--navy); color: var(--royal); }
  .intro-list { position: absolute; left: 46px; top: 128px; list-style: none; }
  .intro-list li, .topic-list li {
    position: relative; padding-left: 22px;
    font-size: 17px; font-weight: 600; color: var(--ink);
  }
  .intro-list li { margin-bottom: 14px; }
  .intro-list li::before, .topic-list li::before {
    content: ""; position: absolute; left: 0; top: 5px;
    width: 11px; height: 11px;
    background: linear-gradient(135deg, var(--bright) 50%, var(--navy) 50%);
  }
  .illustration {
    position: absolute; left: 150px; top: 262px; width: 600px; height: 440px;
    border-radius: 46% 54% 40% 60% / 55% 45% 55% 45%;
    background: radial-gradient(circle at 45% 50%, #a9dcef 0%, #7cc4e6 40%, #5fa7dc 70%, rgba(95,167,220,0) 100%);
  }
  .remote-badge { position: absolute; left: 160px; top: 262px; width: 150px; height: 140px; }
  .course-title { position: absolute; left: 128px; top: 706px; display: flex; align-items: flex-start; }
  .course-number {
    font-family: "Dosis", sans-serif; font-weight: 800;
    font-size: 158px; line-height: 0.85; color: var(--navy); letter-spacing: -6px;
  }
  .course-words { margin-left: 6px; font-family: "Dosis", sans-serif; font-weight: 800; text-transform: uppercase; }
  .course-words .ordinal { display: block; font-size: 26px; line-height: 1; color: var(--navy); }
  .course-words .session { display: block; font-size: 58px; line-height: 0.9; color: var(--navy); }
  .course-words .session span { color: var(--bright); }
  .course-words .start { display: block; margin-top: 8px; font-size: 36px; line-height: 1; color: var(--navy); }
  .topics-pill {
    position: absolute; left: 265px; top: 868px; width: 390px; height: 40px;
    border-radius: 8px; background: var(--bright); color: var(--paper);
    font-weight: 700; font-size: 20px; text-align: center; line-height: 40px;
    text-transform: uppercase;
  }
  .topic-list { position: absolute; top: 944px; list-style: none; }
  .topic-list li { margin-bottom: 14px; font-size: 18px; }
  .col-one { left: 66px; } .col-two { left: 344px; } .col-three { left: 650px; }
  .footer {
    position: absolute; left: 0; bottom: 0; width: 897px; height: 102px;
    background: var(--navy); color: var(--footer-text);
    display: flex; align-items: center; justify-content: center;
    font-size: 23px; font-weight: 600; letter-spacing: 0.3px;
  }
  .footer .sep { margin: 0 14px; }
</style>
</head>
<body>
<main class="poster">
  <svg class="corner-wave" viewBox="0 0 290 270" aria-hidden="true">
    <defs>
      <linearGradient id="waveFill" x1="0" y1="0" x2="1" y2="1">
        <stop offset="0" stop-color="#8a7fd6"/>
        <stop offset="0.5" stop-color="#4ea8d8"/>
        <stop offset="1" stop-color="#4cc3c4"/>
      </linearGradient>
    </defs>
    <path d="M0 0 H290 V270 C270 220 250 140 190 110 C130 80 120 70 60 50 C30 40 10 20 0 0 Z" fill="url(#waveFill)"/>
  </svg>

  <h1 class="headline">Real Estate<br><span class="line-two">Career Course</span></h1>

  <ul class="intro-list">
    <li>How to Make Money In Real Estate?</li>
    <li>For those who have started or would like to go into Real Estate</li>
    <li>An investment in knowledge opens up untold opportunities</li>
  </ul>

  <div class="illustration" role="img" aria-label="Illustration of a young man in a blue suit presenting a white house on a blue abstract backdrop"></div>

  <svg class="remote-badge" viewBox="0 0 150 140" aria-label="Remote Sessions badge">
    <polygon fill="#1f2f6b" points="75,4 88,24 110,12 112,36 138,34 126,56 146,72 124,84 134,108 110,106 104,130 86,114 70,134 60,112 36,124 36,100 12,100 24,78 4,64 26,52 16,30 40,32 44,8 62,24"/>
    <text x="75" y="66" text-anchor="middle" fill="#ffffff" font-family="Dosis, sans-serif" font-weight="800" font-size="21">Remote</text>
    <text x="75" y="88" text-anchor="middle" fill="#ffffff" font-family="Dosis, sans-serif" font-weight="800" font-size="21">Sessions</text>
  </svg>

  <section class="course-title">
    <div class="course-number">12</div>
    <div class="course-words">
      <span class="ordinal">th</span>
      <span class="session">Session <span>Course</span></span>
      <span class="start">Classes starting June 16</span>
    </div>
  </section>

  <div class="topics-pill">A partial listing of topics</div>

  <ul class="topic-list col-one">
    <li>Single-family</li>
    <li>Multifamily</li>
    <li>Management</li>
    <li>Real Estate Concepts</li>
    <li>HUD properties</li>
  </ul>
  <ul class="topic-list col-two">
    <li>Real Estate law</li>
    <li>Investment properties</li>
    <li>Foreclosures</li>
    <li>Rehab</li>
    <li>Due Diligence</li>
  </ul>
  <ul class="topic-list col-three">
    <li>Foreclosures</li>
    <li>Short sales</li>
    <li>Development</li>
    <li>Financial modeling</li>
  </ul>

  <footer class="footer">
    <span>0800 555 014</span><span class="sep">|</span>
    <span>propertypathclass.info</span><span class="sep">|</span>
    <span>propertypathclass.com</span>
  </footer>
</main>
</body>
</html>
```